Business card for Crestline Bathrooms

Please design a business card for our bathroom renovation business. You can use my existing logo, but if you have an idea to modernize it, I would like to see it. Please see attached files first. I would like to use the blue and the orange theme. I like the concept of using the shower head in the logo. Please find following a design (or two) that I have been trying to create with my limited resources. That design was for a sign, but I was going to adopt it and use it as a business card as well. I like the concept of the water splash but I don’t think it “flows” nicely together with the logo. Another thought is that maybe creating the logo out of water splash could work and have a dramatic effect (like the water text and the butterfly picture attached with similar background instead of white). If the above doesn’t work I would like to see a modern simplified design. One of the attached files named as the unwanted business card has all the details that I want included in the business card. Please note that it is two sided.
Updates

I am very thankful for the designs that I have received, but they are very similar and only a couple of attempts to do something with the water splash as per my original brief. Modernizing the logo and having it made out of out of water splash with the orange as color accent could work and have a dramatic effect (like the water text and the butterfly picture attached with similar background instead of white). Please do not use the butterfly itself! This is just an example that images can be created out of water splash.

Contact Information for Business Card

all the details are on the unwonted business card file included

Colors
3176b5

Requirements
Nice to have
• Copied from the brief:
• ... maybe creating the logo out of water splash could work and have a dramatic effect (like the water text and the butterfly picture attached with similar background instead of white). Please do not use the butterfly itself!
Should not have
• I am getting designs with a butterfly. The butterfly picture was an example of creating something from a water splash. The butterfly itself has no association with anything other than the concept of creating a logo out of water splash. Sorry, I thought I was clear in the brief.

```html
<!DOCTYPE html>
<html lang="en">
<head>
<meta charset="utf-8">
<title>Crestline Bathrooms – Business Card</title>
<link href="https://fonts.googleapis.com/css2?family=Roboto:wght@400;500&family=Short+Stack&display=swap" rel="stylesheet">
<style>
  :root {
    --navy: #03426c;
    --coral: #e8715f;
    --card: #f3f3f2;
    --backdrop: #e4e4e3;
    --badge: #6b6b6b;
    --ink-light: #ffffff;
  }
  * { margin: 0; padding: 0; box-sizing: border-box; }
  html, body {
    width: 1200px; height: 960px; overflow: hidden;
    background: var(--backdrop);
    font-family: "Roboto", Arial, sans-serif;
  }
  .canvas { position: relative; width: 1200px; height: 960px; }
  .card {
    position: absolute; width: 600px; height: 343px;
    background: var(--card); overflow: hidden;
  }
  .card--front { left: 314px; top: 113px; }
  .card--back { left: 311px; top: 472px; }
  .card__shape { position: absolute; inset: 0; width: 600px; height: 343px; }

  .holder-name {
    position: absolute; left: 43px; top: 48px;
    font-family: "Short Stack", "Comic Neue", cursive;
    font-size: 23px; color: var(--coral); letter-spacing: 0.5px;
  }
  .contact-list { position: absolute; left: 43px; top: 178px; list-style: none; }
  .contact-item {
    display: flex; align-items: flex-start; gap: 9px;
    color: var(--ink-light); font-size: 14px; line-height: 19px;
  }
  .contact-item + .contact-item { margin-top: 0; }
  .contact-item--address { margin-bottom: 9px; }
  .contact-icon { width: 13px; height: 13px; margin-top: 3px; flex: none; }

  .wordmark {
    position: absolute; left: 358px; top: 150px;
    display: flex; align-items: center; gap: 12px;
  }
  .wordmark__dot { width: 18px; height: 18px; border-radius: 50%; background: var(--coral); flex: none; }
  .wordmark__name {
    font-family: "Roboto", Arial, sans-serif; font-weight: 500;
    font-size: 30px; line-height: 32px; color: var(--navy);
  }

  .service-list { position: absolute; left: 34px; top: 46px; list-style: none; }
  .service-item {
    position: relative; padding-left: 17px;
    color: var(--ink-light); font-size: 14px; line-height: 19px;
    margin-bottom: 19px;
  }
  .service-item::before {
    content: ""; position: absolute; left: 0; top: 6px;
    width: 6px; height: 6px; border-radius: 50%; background: var(--coral);
  }
  .affiliations {
    position: absolute; left: 356px; top: 268px;
    display: flex; align-items: center; gap: 16px;
  }
  .affiliation-badge { background: var(--badge); border-radius: 5px; }
  .affiliation-badge--round { width: 22px; height: 36px; border-radius: 6px; }
  .affiliation-badge--wide { width: 28px; height: 24px; border-radius: 2px; }
  .affiliation-divider { width: 1px; height: 40px; background: var(--badge); }
</style>
</head>
<body>
<main class="canvas">

  <section class="card card--front" aria-label="Business card front">
    <svg class="card__shape" viewBox="0 0 600 343" aria-hidden="true">
      <rect width="600" height="343" fill="var(--navy)"/>
      <path d="M367,343 C300,280 215,215 228,160 C242,100 330,58 440,55 C520,53 560,75 575,110 L600,104 L600,343 Z" fill="var(--card)"/>
    </svg>

    <p class="holder-name">Daniel Marrovic</p>

    <ul class="contact-list">
      <li class="contact-item contact-item--address">
        <svg class="contact-icon" viewBox="0 0 12 12"><path d="M6 0.5a4 4 0 0 0-4 4c0 3 4 7 4 7s4-4 4-7a4 4 0 0 0-4-4zm0 5.6a1.6 1.6 0 1 1 0-3.2 1.6 1.6 0 0 1 0 3.2z" fill="var(--coral)"/></svg>
        <span>PO Box 418<br>Brindlewood 2743</span>
      </li>
      <li class="contact-item">
        <svg class="contact-icon" viewBox="0 0 12 12"><path d="M2.5 0.8l2 2.2-1 1.4c.6 1.5 1.7 2.6 3.2 3.2l1.4-1 2.2 2-1 2C6 10.4 1.6 6 0.6 2z" fill="var(--coral)"/></svg>
        <span>0400 555 218</span>
      </li>
      <li class="contact-item">
        <svg class="contact-icon" viewBox="0 0 12 12"><rect x="3" y="0.5" width="6" height="11" rx="1.2" fill="none" stroke="var(--coral)" stroke-width="1.4"/><circle cx="6" cy="9.5" r="0.8" fill="var(--coral)"/></svg>
        <span>5550 1947</span>
      </li>
      <li class="contact-item">
        <svg class="contact-icon" viewBox="0 0 12 12"><rect x="0.5" y="2.5" width="11" height="7.5" rx="1" fill="var(--coral)"/><path d="M1 3l5 4 5-4" fill="none" stroke="var(--navy)" stroke-width="1"/></svg>
        <span>daniel@crestlinebathrooms.com.au</span>
      </li>
      <li class="contact-item">
        <svg class="contact-icon" viewBox="0 0 12 12"><circle cx="6" cy="6" r="5.5" fill="var(--coral)"/><path d="M0.5 6h11M6 0.5c-2.5 3-2.5 8 0 11M6 0.5c2.5 3 2.5 8 0 11" fill="none" stroke="var(--navy)" stroke-width="0.8"/></svg>
        <span>crestlinebathrooms.com.au</span>
      </li>
    </ul>

    <div class="wordmark">
      <span class="wordmark__dot"></span>
      <span class="wordmark__name">Crestline<br>Bathrooms</span>
    </div>
  </section>

  <section class="card card--back" aria-label="Business card back">
    <svg class="card__shape" viewBox="0 0 600 343" aria-hidden="true">
      <rect width="600" height="343" fill="var(--navy)"/>
      <path d="M368,0 C410,40 430,90 425,130 C415,230 330,290 200,315 C140,326 110,334 95,343 L600,343 L600,0 Z" fill="var(--card)"/>
    </svg>

    <ul class="service-list">
      <li class="service-item">Complete Bathroom Renovations<br>&amp; Remodelling</li>
      <li class="service-item">Highly Skilled &amp;<br>Qualified Tradespeople</li>
      <li class="service-item">Professional Service From<br>Concept To Completion</li>
      <li class="service-item">All Work Guaranteed</li>
    </ul>

    <div class="affiliations" aria-label="Industry memberships">
      <span class="affiliation-badge affiliation-badge--round"></span>
      <span class="affiliation-divider"></span>
      <span class="affiliation-badge affiliation-badge--wide"></span>
    </div>
  </section>

</main>
</body>
</html>
```